Grey Fennel Medical Website to make connecting and communicating easier

To create a unique, user-friendly, professional website for patients and professionals to access education/ information, forms, appointments, contact details, and data about us, and for us to have the capacity to link to various cloud-based platforms.
To use the logo design and colour scheme we have just sourced.

WEBSITE to be eye catching, Inspiring and alluring
- efficient and logical
- professional and trustworthy appearance
- health focus "living health matters"
- user friendly
- ability to link with cloud-based software and video conferencing tools/ telehealth
- colours- black/ white teal and ?silver

PAGES:
page 1 - Our clinic and staff, services offered, contact us- address/ map / contact details- social media connections
page 2- patients and visitors - New patient forms to complete, news and patient informtion (educatinal)
page 3 - health professionals -referral forms, research and education
page 3- online appointments
page 4 - Quick links - partners, other services
page 5- privacy policy, disclaimer

HI, Could we please extend the deadline another 5 days, so sorry just struggling with my workload to be able to keep up and I am wanting to liaise more with the designer that I will choose. I am so happy with SketchHarbor and all the designers - thank you! Thank you so much!!

Target Market(s)

Patients - mostly over 60's so the website must be minimal clicks and simple to navigate
Professionals - for education and access forms

Industry/Entity Type

Health Care

Coding

Coded - Design and coding required

Number of Pages Required

5+ page

Font styles to use
Sans Serif
Script

Colors
33b8a4
86cfc6

Requirements
Must have
• WEBSITE to be eye catching, Inspiring and alluring
- efficient and logical
- user friendly

WEBSITE - professional and user friendly
- ability to link with cloud based software and videoconferencing/ telehealth
Nice to have
• clean and crisp presentation
happy for an innovative look
room to add more services and ability to link pages and resources
Should not have
• Please ensure the website is not:
clunky
difficult to navigate
common and cheap looking

```html
<!DOCTYPE html>
<html lang="en">
<head>
<meta charset="utf-8">
<title>Grey Fennel Medical</title>
<link href="https://fonts.googleapis.com/css2?family=Audiowide&family=Lato:wght@400;700;900&display=swap" rel="stylesheet">
<style>
:root{
  --teal:#2aa58f;
  --teal-light:#86cfc6;
  --teal-pale:#e6f4f1;
  --ink:#111;
  --text:#555;
  --grey-bg:#f3f3f3;
  --map:#8a8a8a;
  --white:#fff;
  --black:#000;
}
*{margin:0;padding:0;box-sizing:border-box}
html,body{width:1200px;height:3548px;overflow:hidden;background:var(--white)}
body{font-family:'Lato',sans-serif;color:var(--text)}
.page{position:relative;width:1200px;height:3548px;overflow:hidden}
.abs{position:absolute}
.display{font-family:'Audiowide',sans-serif;color:var(--ink);font-weight:400}
.btn{position:absolute;background:var(--teal);color:var(--white);font:700 15px 'Lato',sans-serif;display:flex;align-items:center;justify-content:center;gap:7px;text-transform:uppercase}
.btn .dot{width:12px;height:12px;border-radius:50%;background:var(--white);position:relative}
.btn .dot::after{content:"";position:absolute;left:3px;top:3px;border-left:6px solid var(--teal);border-top:3px solid transparent;border-bottom:3px solid transparent}
.underline{position:absolute;height:3px;width:36px;background:var(--teal)}

/* header */
.brand{left:143px;top:30px;display:flex;align-items:center;gap:10px;font:900 20px 'Lato',sans-serif;color:var(--teal)}
.brand .mark{width:34px;height:34px;border-radius:50%;background:var(--teal)}
.call{left:595px;top:14px;display:flex;align-items:center;gap:10px;font:700 20px 'Lato',sans-serif;color:#222}
.call .ring{width:36px;height:36px;border-radius:50%;border:2px solid var(--teal);display:flex;align-items:center;justify-content:center}
.social{display:flex;gap:6px}
.social span{width:28px;height:28px;border-radius:50%}
.s1{background:#1e3a73}.s2{background:#1da1f2}.s3{background:#e02a20}.s4{background:#a07a45}.s5{background:#0e5a8a}
.header-social{left:890px;top:18px}
.nav{left:360px;top:65px;width:840px;height:44px;background:var(--teal);clip-path:polygon(28px 0,100% 0,100% 100%,0 100%)}
.nav ul{list-style:none;display:flex;height:100%;align-items:center;padding-left:30px}
.nav li{color:var(--white);font:700 13.5px 'Lato',sans-serif;padding:0 8px;height:100%;display:flex;align-items:center}
.nav li.active{background:var(--teal-light);padding:0 18px;margin-right:8px}

/* hero */
.hero-photo{left:0;top:110px;width:1200px;height:600px;background:linear-gradient(100deg,#5f7896 0%,#8fa3b4 30%,#c79a66 60%,#d8a46a 80%,#b47d4a 100%)}
.hero-bar{left:144px;top:220px;width:3px;height:208px;background:var(--teal)}
.hero-title{left:181px;top:222px;font-size:58px;line-height:70px;color:var(--white);white-space:nowrap}
.hero-sub{left:181px;top:452px;font-size:20px;color:var(--white)}
.hero-dots{left:1128px;top:355px;display:flex;flex-direction:column;gap:7px}
.hero-dots span{width:8px;height:8px;border-radius:50%;background:var(--white)}
.hero-dots span.on{background:var(--teal-light)}

/* about */
.about-title{left:165px;top:780px;font-size:40px;line-height:52px}
.about-text{left:494px;top:785px;width:530px;font-size:13px;line-height:26.4px;color:#444}

/* team */
.member{position:absolute;width:240px;text-align:center}
.member .ring{width:240px;height:240px;border-radius:50%;border:3px solid var(--teal);display:flex;align-items:center;justify-content:center;background:var(--white)}
.member .photo{width:188px;height:188px;border-radius:50%}
.member h3{margin-top:30px;font:700 20px 'Lato',sans-serif;color:#222}
.member p{margin-top:10px;font-size:13px;line-height:20px;color:#555}
.chev{position:absolute}

/* services */
.services-bg{left:0;top:1490px;width:1200px;height:820px}
.services-title{left:0;width:1200px;top:1668px;text-align:center;font-size:40px}
.card{position:absolute;width:288px;height:350px}
.card .img{position:absolute;left:0;top:0;width:288px;height:190px}
.card .box{position:absolute;left:11px;top:165px;width:266px;height:181px;background:var(--white);box-shadow:0 3px 8px rgba(0,0,0,.15);text-align:center}
.card .icon{position:absolute;left:107px;top:-36px;width:52px;height:52px;border-radius:50%;background:var(--white);display:flex;align-items:center;justify-content:center;border-top:3px solid var(--teal)}
.card h3{margin-top:38px;font:400 18px 'Lato',sans-serif;color:#222}
.card p{margin:12px auto 0;width:222px;font-size:11px;line-height:21px;color:#666}
.card .more{margin-top:10px;font:700 11.5px 'Lato',sans-serif;color:var(--teal);display:flex;justify-content:center;align-items:center;gap:5px}
.card .more i{width:10px;height:10px;border-radius:50%;background:var(--teal);display:inline-block}
.arrow-circle{position:absolute;width:44px;height:44px;border-radius:50%;border:1.5px solid #555;display:flex;align-items:center;justify-content:center;background:var(--white)}

/* appointment */
.book-title{left:0;width:1200px;top:2363px;text-align:center;font-size:40px}
.info{position:absolute;display:flex;align-items:center;gap:16px;font-size:13.5px;line-height:21px;color:#555}
.info .ic{width:50px;height:50px;border-radius:50%;background:var(--teal);display:flex;align-items:center;justify-content:center;flex:none}
.info .ic.soft{background:var(--teal-light)}
.map{left:146px;top:2593px;width:908px;height:467px;background:linear-gradient(135deg,#9a9a9a,#7e7e7e 60%,#8e8e8e)}
.field{position:absolute;background:var(--white);font-size:13.5px;color:#444;padding:20px 21px}

/* footer */
.footer-logo{left:184px;top:3326px;font:900 18px 'Lato',sans-serif;color:var(--teal);display:flex;align-items:center;gap:10px;white-space:nowrap}
.footer-logo .mark{width:36px;height:36px;border-radius:50%;background:var(--teal)}
.footer-call{left:440px;top:3300px;display:flex;align-items:center;gap:14px;color:var(--white)}
.footer-call .ring{width:44px;height:44px;border-radius:50%;border:2px solid var(--teal);display:flex;align-items:center;justify-content:center}
.footer-call small{display:block;font:700 23px 'Lato',sans-serif}
.footer-call b{display:block;font:700 32px 'Lato',sans-serif}
.footer-social{left:770px;top:3315px;gap:11px}
.footer-social span{width:42px;height:42px}
.footer-rule{left:0;top:3428px;width:1200px;height:1px;background:#1e1e1e}
.footer-nav{left:0;width:1200px;top:3462px;text-align:center;color:var(--white);font:700 15px 'Lato',sans-serif;word-spacing:2px}
.copyright{left:0;width:1200px;top:3504px;text-align:center;color:var(--white);font-size:11.5px}
</style>
</head>
<body>
<div class="page">

  <!-- header -->
  <div class="abs brand"><span class="mark"></span>Grey Fennel Medical</div>
  <div class="abs call">
    <span class="ring"><svg width="18" height="18" viewBox="0 0 24 24"><path d="M6.6 10.8a15 15 0 0 0 6.6 6.6l2.2-2.2c.3-.3.7-.4 1-.2 1.1.4 2.3.6 3.6.6.6 0 1 .4 1 1V20c0 .6-.4 1-1 1A17 17 0 0 1 3 4c0-.6.4-1 1-1h3.5c.6 0 1 .4 1 1 0 1.3.2 2.5.6 3.6.1.3 0 .7-.2 1z" fill="#2aa58f"/></svg></span>
    Call Us : 1 888 888 8888
  </div>
  <div class="abs social header-social" aria-label="Social media links"><span class="s1"></span><span class="s2"></span><span class="s3"></span><span class="s4"></span><span class="s5"></span></div>
  <nav class="abs nav">
    <ul>
      <li class="active">Home</li><li>Patients and visitors</li><li>Health professionals</li><li>Online appointments</li><li>Quick links</li><li>Privacy policy</li>
    </ul>
  </nav>

  <!-- hero -->
  <div class="abs hero-photo" role="img" aria-label="Smiling nurse in blue scrubs with a stethoscope in a bright clinic corridor"></div>
  <svg class="abs" style="left:0;top:600px" width="1200" height="115" viewBox="0 0 1200 115">
    <path d="M0 115 L0 108 Q300 80 600 18 Q900 80 1200 98 L1200 115 Z" fill="#fff"/>
    <path d="M330 60 Q470 40 600 18 Q760 52 1010 80" stroke="#2aa58f" stroke-width="6" fill="none"/>
  </svg>
  <div class="abs hero-bar"></div>
  <h1 class="abs display hero-title">GREY<br>FENNEL<br>MEDICAL</h1>
  <p class="abs hero-sub">Lorem ipsum dolor sit amconsectetur adipiscing</p>
  <div class="btn" style="left:183px;top:512px;width:166px;height:45px">Get started <span class="dot"></span></div>
  <div class="abs hero-dots"><span></span><span></span><span class="on"></span><span></span><span></span></div>

  <!-- about -->
  <h2 class="abs display about-title">ABOUT<br>OUR CLINIC</h2>
  <div class="underline" style="left:165px;top:890px"></div>
  <p class="abs about-text">Lorem ipsum dolor sit amet, consectetur adipiscing elit, sed do eiusmod tempor incididunt ut labore et dolore magna aliquis ipsum suspendisse ultrices grs commodo viverra maecenas accumsan lacus vel facilisis. Lorem ipsum dolor sit amet, consectetur adipiscing elit, sed do eiusmod tempor incididunt ut labore et dolore magna aliquis ipsum suspen disse ultrices grs commodo viverra maecenas accumsan lacus vel fem</p>
  <div class="btn" style="left:494px;top:944px;width:148px;height:44px">Read more <span class="dot"></span></div>

  <!-- team -->
  <svg class="chev" style="left:76px;top:1195px" width="32" height="66" viewBox="0 0 32 66"><path d="M30 2 L2 33 L30 64" stroke="#999" stroke-width="2" fill="none"/></svg>
  <svg class="chev" style="left:1092px;top:1195px" width="32" height="66" viewBox="0 0 32 66"><path d="M2 2 L30 33 L2 64" stroke="#999" stroke-width="2" fill="none"/></svg>
  <div class="member" style="left:144px;top:1107px">
    <div class="ring"><div class="photo" role="img" aria-label="Portrait of a male doctor with arms crossed" style="background:linear-gradient(160deg,#e8e8e8,#c9c9c9)"></div></div>
    <h3>ALAN REED</h3><p>Sed ut perspiciatis unmnis<br>iste natus</p>
  </div>
  <div class="member" style="left:480px;top:1107px">
    <div class="ring"><div class="photo" role="img" aria-label="Portrait of a smiling male doctor in a white coat" style="background:linear-gradient(160deg,#6f9cc4,#3e6f9e)"></div></div>
    <h3>DANA MORROW</h3><p>Sed ut perspiciatis unmnis<br>iste natus</p>
  </div>
  <div class="member" style="left:816px;top:1107px">
    <div class="ring"><div class="photo" role="img" aria-label="Portrait of a female doctor with a stethoscope" style="background:linear-gradient(160deg,#eef1f4,#cdd6de)"></div></div>
    <h3>YUNA GRANT</h3><p>Sed ut perspiciatis unmnis<br>iste natus</p>
  </div>

  <!-- services -->
  <svg class="abs services-bg" width="1200" height="820" viewBox="0 0 1200 820">
    <path d="M0 10 Q150 100 420 100 Q900 90 1060 30 Q1150 0 1200 90 L1200 785 Q1100 740 980 730 Q700 720 300 810 Q80 820 0 730 Z" fill="#f3f3f3"/>
    <path d="M0 10 Q120 90 420 100" stroke="#5fb9ac" stroke-width="5" fill="none"/>
    <path d="M950 725 Q1100 730 1200 790" stroke="#2aa58f" stroke-width="5" fill="none"/>
  </svg>
  <h2 class="abs display services-title">SERVICES OFFERED</h2>
  <div class="underline" style="left:582px;top:1730px"></div>

  <div class="arrow-circle" style="left:68px;top:1934px"><svg width="14" height="20" viewBox="0 0 14 20"><path d="M11 2 L3 10 L11 18" stroke="#444" stroke-width="2" fill="none"/></svg></div>
  <div class="arrow-circle" style="left:1088px;top:1934px"><svg width="14" height="20" viewBox="0 0 14 20"><path d="M3 2 L11 10 L3 18" stroke="#444" stroke-width="2" fill="none"/></svg></div>

  <div class="card" style="left:145px;top:1787px">
    <div class="img" role="img" aria-label="Doctor talking with a patient" style="background:linear-gradient(120deg,#d9e2ea,#8aa6bf 50%,#b9bcbf)"></div>
    <div class="box">
      <div class="icon"><svg width="30" height="30" viewBox="0 0 30 30"><rect x="3" y="4" width="24" height="17" fill="none" stroke="#333" stroke-width="1.6"/><path d="M11 26h8M15 21v5" stroke="#333" stroke-width="1.6"/></svg></div>
      <h3>Ullamco laboris</h3><p>Lorem ipsum dolor sit ametonsectetur adipiscing elit, sed do eiusmod tempor incididunt ut labore</p>
      <div class="more">READ MORE <i></i></div>
    </div>
  </div>
  <div class="card" style="left:456px;top:1787px">
    <div class="img" role="img" aria-label="Doctor working at a laptop by a window" style="background:linear-gradient(120deg,#cfd2d0,#7d8784 50%,#b8b4ac)"></div>
    <div class="box">
      <div class="icon"><svg width="30" height="30" viewBox="0 0 30 30"><circle cx="15" cy="9" r="5" fill="none" stroke="#333" stroke-width="1.6"/><path d="M5 28c0-7 4-11 10-11s10 4 10 11" fill="none" stroke="#333" stroke-width="1.6"/></svg></div>
      <h3>Excepteur sint</h3><p>Lorem ipsum dolor sit ametonsectetur adipiscing elit, sed do eiusmod tempor incididunt ut labore</p>
      <div class="more">READ MORE <i></i></div>
    </div>
  </div>
  <div class="card" style="left:767px;top:1787px">
    <div class="img" role="img" aria-label="Smiling patient speaking with a nurse" style="background:linear-gradient(120deg,#c9b8a8,#a88d78 45%,#5f7f9c)"></div>
    <div class="box">
      <div class="icon"><svg width="30" height="30" viewBox="0 0 30 30"><circle cx="13" cy="9" r="5" fill="none" stroke="#333" stroke-width="1.6"/><path d="M3 28c0-7 4-11 10-11" fill="none" stroke="#333" stroke-width="1.6"/><circle cx="22" cy="22" r="5" fill="none" stroke="#333" stroke-width="1.6"/><path d="M22 19v6M19 22h6" stroke="#333" stroke-width="1.6"/></svg></div>
      <h3>Duis aute irure</h3><p>Lorem ipsum dolor sit ametonsectetur adipiscing elit, sed do eiusmod tempor incididunt ut labore</p>
      <div class="more">READ MORE <i></i></div>
    </div>
  </div>

  <!-- appointment -->
  <h2 class="abs display book-title">BOOK AN APPOINTMENT</h2>
  <div class="underline" style="left:582px;top:2427px"></div>

  <div class="info" style="left:196px;top:2487px">
    <span class="ic"><svg width="16" height="22" viewBox="0 0 16 22"><path d="M8 0a8 8 0 0 0-8 8c0 6 8 14 8 14s8-8 8-14a8 8 0 0 0-8-8z" fill="#fff"/><circle cx="8" cy="8" r="3" fill="#2aa58f"/></svg></span>
    <span>234,Lorem ipsum dolor sit amet<br>consectetur adipiscing elit,</span>
  </div>
  <div class="info" style="left:494px;top:2487px">
    <span class="ic soft"><svg width="20" height="20" viewBox="0 0 24 24"><path d="M6.6 10.8a15 15 0 0 0 6.6 6.6l2.2-2.2c.3-.3.7-.4 1-.2 1.1.4 2.3.6 3.6.6.6 0 1 .4 1 1V20c0 .6-.4 1-1 1A17 17 0 0 1 3 4c0-.6.4-1 1-1h3.5c.6 0 1 .4 1 1 0 1.3.2 2.5.6 3.6.1.3 0 .7-.2 1z" fill="#fff"/></svg></span>
    <span>Phone : 1 888 888 8888</span>
  </div>
  <div class="info" style="left:744px;top:2487px">
    <span class="ic"><svg width="22" height="16" viewBox="0 0 22 16"><rect width="22" height="16" rx="2" fill="#fff"/><path d="M1 2l10 7 10-7" stroke="#2aa58f" stroke-width="2" fill="none"/></svg></span>
    <span>info@greyfennelmedical.com</span>
  </div>

  <div class="abs map" role="img" aria-label="Map of north-west Europe with a location marker"></div>
  <div class="field" style="left:234px;top:2688px;width:358px;height:52px">First Name</div>
  <div class="field" style="left:606px;top:2688px;width:359px;height:52px">Last Name</div>
  <div class="field" style="left:234px;top:2753px;width:358px;height:52px">Email address</div>
  <div class="field" style="left:606px;top:2753px;width:359px;height:52px">Phone Number</div>
  <div class="field" style="left:234px;top:2818px;width:731px;height:114px">Message</div>
  <div class="btn" style="left:526px;top:2972px;width:148px;height:42px">Submit <span class="dot"></span></div>

  <!-- footer -->
  <svg class="abs" style="left:0;top:3150px" width="1200" height="398" viewBox="0 0 1200 398">
    <path d="M0 18 Q300 0 600 78 Q900 0 1200 18 L1200 398 L0 398 Z" fill="#000"/>
    <path d="M180 12 Q420 20 600 78 Q780 20 1020 12" stroke="#2aa58f" stroke-width="5" fill="none"/>
    <circle cx="600" cy="78" r="32" fill="#2aa58f" stroke="#fff" stroke-width="4"/>
    <path d="M600 96 V60 M586 74 L600 60 L614 74" stroke="#fff" stroke-width="4" fill="none"/>
  </svg>
  <div class="abs footer-logo"><span class="mark"></span>Grey Fennel Medical</div>
  <div class="abs footer-call">
    <span class="ring"><svg width="20" height="20" viewBox="0 0 24 24"><path d="M6.6 10.8a15 15 0 0 0 6.6 6.6l2.2-2.2c.3-.3.7-.4 1-.2 1.1.4 2.3.6 3.6.6.6 0 1 .4 1 1V20c0 .6-.4 1-1 1A17 17 0 0 1 3 4c0-.6.4-1 1-1h3.5c.6 0 1 .4 1 1 0 1.3.2 2.5.6 3.6.1.3 0 .7-.2 1z" fill="#2aa58f"/></svg></span>
    <span><small>Call Us</small><b>1 888 888 8888</b></span>
  </div>
  <div class="abs social footer-social" aria-label="Social media links"><span class="s1"></span><span class="s2"></span><span class="s3"></span><span class="s4"></span><span class="s5"></span></div>
  <div class="abs footer-rule"></div>
  <div class="abs footer-nav">HOME &nbsp;/&nbsp; PATIENTS AND VISITORS &nbsp;/&nbsp; HEALTH PROFESSIONALS &nbsp;/&nbsp; ONLINE APPOINTMENTS &nbsp;/&nbsp; QUICK LINKS &nbsp;/&nbsp; PRIVACY POLICY</div>
  <div class="abs copyright">© 2020 Grey Fennel Medical.All Rights reserved &nbsp;| Privacy Policy &nbsp;| &nbsp;disclaimer</div>

</div>
</body>
</html>
```